Poloshirt Packaging

We need a very attractive packaging design for our poloshirts. We are wholesaler of the schoolwear market. See what we currently have. I dont want any specific sizing put on the packaging. One design for all poloshirts (2 sides).
our logo is attached aswell

Target Market(s)

Parents

Requirements
Must have
• Our logo
Should not have
• size or age

```html
<!DOCTYPE html>
<html lang="en">
<head>
<meta charset="utf-8">
<title>Brightway Poloshirt Packaging</title>
<link rel="stylesheet" href="https://fonts.googleapis.com/css2?family=Poppins:wght@500;600;700&family=Roboto+Condensed:wght@400;700&display=swap">
<style>
  :root {
    --navy: #173a63;
    --red: #e2202f;
    --orange: #ef7a22;
    --yellow: #f7c21a;
    --paper: #ffffff;
    --rule: #3a3a3a;
    --ink: #222222;
  }
  * { margin: 0; padding: 0; box-sizing: border-box; }
  html, body { width: 1200px; height: 849px; overflow: hidden; background: var(--paper); }
  .canvas { position: relative; width: 1200px; height: 849px; background: var(--paper); overflow: hidden; }
  .waves { position: absolute; inset: 0; width: 1200px; height: 849px; }
  .brand-name {
    position: absolute;
    font-family: "Poppins", sans-serif;
    font-weight: 600;
    color: var(--navy);
    font-size: 86px;
    line-height: 1;
    letter-spacing: 1px;
  }
  .product-name {
    position: absolute;
    font-family: "Poppins", sans-serif;
    font-weight: 700;
    color: var(--red);
    font-size: 44px;
    line-height: 1;
    letter-spacing: 1px;
  }
  .front .brand-name { left: 52px; top: 542px; }
  .front .product-name { left: 54px; top: 630px; }
  .feature-bar {
    position: absolute;
    left: 57px; top: 691px;
    width: 375px; height: 21px;
    background: var(--navy);
    color: var(--paper);
    font-family: "Poppins", sans-serif;
    font-weight: 600;
    font-size: 11.5px;
    line-height: 21px;
    padding-left: 7px;
    white-space: nowrap;
  }
  .back .brand-name { left: 601px; width: 600px; text-align: center; top: 242px; }
  .back .product-name { left: 601px; width: 600px; text-align: center; top: 384px; }
  .facts {
    position: absolute;
    left: 601px; width: 600px; top: 624px;
    text-align: center;
    font-family: "Roboto Condensed", sans-serif;
    font-size: 11.5px;
    line-height: 18px;
    color: var(--ink);
    list-style: none;
  }
  .facts .facts-title { font-weight: 700; }
  .thanks-box {
    position: absolute;
    left: 710px; top: 735px;
    width: 373px; height: 49px;
    background: var(--navy);
    color: var(--paper);
    font-family: "Roboto Condensed", sans-serif;
    font-weight: 700;
    font-size: 12.5px;
    line-height: 17px;
    text-align: center;
    padding-top: 8px;
  }
</style>
</head>
<body>
<div class="canvas">
  <svg class="waves" viewBox="0 0 992 702" preserveAspectRatio="none" aria-hidden="true">
    <defs>
      <linearGradient id="front-sweep" x1="0" y1="0" x2="1" y2="0">
        <stop offset="0" stop-color="#e53f29"/>
        <stop offset="0.55" stop-color="#ef8a1f"/>
        <stop offset="1" stop-color="#f6bd1a"/>
      </linearGradient>
      <linearGradient id="back-sweep" x1="0" y1="0" x2="1" y2="0">
        <stop offset="0" stop-color="#f9d900"/>
        <stop offset="0.4" stop-color="#f6a91a"/>
        <stop offset="0.8" stop-color="#ec6b24"/>
        <stop offset="1" stop-color="#e2342a"/>
      </linearGradient>
    </defs>
    <!-- front panel -->
    <path class="front-band" fill="url(#front-sweep)"
      d="M0,342 C120,300 240,320 330,235 C380,188 410,132 455,140 C475,145 488,170 497,185 L497,218 C470,190 440,180 400,222 C330,295 255,342 170,360 C95,375 40,392 0,422 Z"/>
    <path class="front-ribbon" fill="var(--red)"
      d="M370,702 C395,655 440,598 497,586 L497,640 C462,650 432,680 420,702 Z"/>
    <!-- back panel -->
    <path class="back-band" fill="url(#back-sweep)"
      d="M497,352 C565,372 625,396 700,396 C800,396 870,352 992,362 L992,440 C885,420 820,470 720,490 C630,506 560,482 497,442 Z"/>
    <path class="back-ribbon" fill="var(--red)"
      d="M820,702 C840,660 870,610 905,604 C932,600 962,614 992,624 L992,642 C962,632 936,620 915,628 C890,640 852,680 838,702 Z"/>
    <!-- panel edges -->
    <rect x="0.5" y="0.5" width="495.5" height="701" fill="none" stroke="var(--rule)" stroke-width="1"/>
    <rect x="497" y="0.5" width="494.5" height="701" fill="none" stroke="var(--rule)" stroke-width="1"/>
  </svg>

  <section class="panel front">
    <h1 class="brand-name">Brightway</h1>
    <h2 class="product-name">POLOSHIRT</h2>
    <p class="feature-bar">Superior weight fabric &nbsp;|&nbsp; Easy Care - Low iron &nbsp;|&nbsp; Reactive Dyes</p>
  </section>

  <section class="panel back">
    <h1 class="brand-name">Brightway</h1>
    <h2 class="product-name">POLOSHIRT</h2>
    <ul class="facts">
      <li class="facts-title">Did you know</li>
      <li>This Poloshirt Is Sold In 12 Colours</li>
      <li>Reactive Dyed For Superb Colour Fastness</li>
      <li>A Superior Weight Of 210gms</li>
      <li>Strengthened With Twin Needle Stitching</li>
    </ul>
    <p class="thanks-box">Thanks You for Buying Our Product and<br>Ask your Local Supplier abt the Rest Of Brightway Range</p>
  </section>
</div>
</body>
</html>
```